Cover Art for Song "Driftin by Night" by Dale Pormick

Link to song
https://www.tunevaultsite.com/dalepormicktheporchstars

Lyrics:
Driftin’ by Night

Verse:
I lost my way
and I can’t be found
Gettin too old,
a little run-down
Always in trouble Gonna pick things up
Trouble finds me
Wherever I am
Need a new direction
Need a new plan
Gonna make a change
Pre Chorus
some don’t see it and
others don’t know
listen on up
I’m moving on down
I'm movin down
Chorus
Im Driftin by Night to the Everglades
where nobody seems to make
a big deal who I am

Target Market(s)

Country Music

Industry/Entity Type

Music

```html
<!DOCTYPE html>
<html lang="en">
<head>
<meta charset="utf-8">
<title>Driftin by Night – Dale Pormick</title>
<link rel="stylesheet" href="https://fonts.googleapis.com/css2?family=Kaushan+Script&family=Oswald:wght@500;600&display=swap">
<style>
  :root {
    --stage: #d6d8d3;
    --truck-red: #8e1f22;
    --truck-deep: #5e1214;
    --sky-light: #e9ebe2;
    --foliage: #7d8a5a;
    --chrome: #c9ccd0;
    --plate: #ecebdc;
    --plate-rim: #b9a98f;
    --plate-ink: #16181a;
    --title-white: #ffffff;
  }
  html, body {
    margin: 0;
    width: 1200px;
    height: 1030px;
    overflow: hidden;
    background: var(--stage);
  }
  .cover {
    position: absolute;
    left: 100px;
    top: 15px;
    width: 1000px;
    height: 1000px;
    overflow: hidden;
  }
  .cover-photo {
    position: absolute;
    inset: 0;
    background:
      linear-gradient(180deg, transparent 0%, transparent 86%, var(--chrome) 90%, #8d9096 96%, var(--chrome) 100%),
      linear-gradient(180deg, var(--sky-light) 0%, var(--foliage) 12%, var(--truck-red) 24%, var(--truck-red) 40%, var(--truck-deep) 43%, var(--truck-red) 47%, var(--truck-red) 84%, var(--truck-deep) 88%);
  }
  .artist-name {
    position: absolute;
    margin: 0;
    font-family: "Kaushan Script", cursive;
    font-weight: 400;
    color: var(--title-white);
    line-height: 1;
    white-space: nowrap;
    transform: rotate(-4deg);
    transform-origin: left center;
    text-shadow: 0 4px 10px rgba(0,0,0,0.35);
  }
  .artist-first { left: 80px; top: 70px; font-size: 200px; }
  .artist-last  { left: 285px; top: 280px; font-size: 175px; }
  .plate {
    position: absolute;
    left: 180px;
    top: 521px;
    width: 634px;
    height: 256px;
    box-sizing: border-box;
    background: var(--plate);
    border: 8px solid var(--plate-rim);
    border-radius: 18px;
    box-shadow: 0 6px 14px rgba(0,0,0,0.45);
    text-align: center;
    color: var(--plate-ink);
    font-family: "Oswald", sans-serif;
  }
  .plate-state {
    margin-top: 30px;
    font-size: 36px;
    font-weight: 500;
    letter-spacing: 2px;
    line-height: 1;
  }
  .plate-title {
    margin-top: 16px;
    font-size: 88px;
    font-weight: 600;
    line-height: 1;
    letter-spacing: 1px;
    white-space: nowrap;
  }
  .plate-title .small-word {
    font-size: 26px;
    vertical-align: middle;
    margin: 0 6px;
  }
  .plate-bolt {
    position: absolute;
    width: 14px;
    height: 14px;
    border-radius: 50%;
    background: #8f8f88;
  }
</style>
</head>
<body>
  <main class="cover">
    <div class="cover-photo" role="img" aria-label="Rear view of a weathered red vintage pickup truck with chrome bumper, palm trees blurred behind"></div>
    <h1 class="artist-name artist-first">Dale</h1>
    <h1 class="artist-name artist-last">Pormick</h1>
    <div class="plate">
      <span class="plate-bolt" style="left:120px;top:14px"></span>
      <span class="plate-bolt" style="right:120px;top:14px"></span>
      <span class="plate-bolt" style="left:120px;bottom:14px"></span>
      <span class="plate-bolt" style="right:120px;bottom:14px"></span>
      <div class="plate-state">FLORIDA</div>
      <div class="plate-title">DRIFTIN<span class="small-word">BY</span>NIGHT</div>
    </div>
  </main>
</body>
</html>
```